Business Card Design Project

Company Name - Solvane Care

Wellness consulting and training company. Run through a medical centre.

Main colour themes are orange and blue, as in the logo. Want to replicate same effect with business cards.

To give a sense of freedom and potential as per the company name.

Want the business card to be in line with stationary design, which I have launched as well.

Double sided with design and colour on one side and details on other side.

Reason: Need business card and stationary design to be teed up.

Target Market(s)

35 to 65 age group.
New age and trendy

Industry/Entity Type

Training

Requirements
Must have
• Colours orange and blue as per logo
Nice to have
• Design to be similar to stationary design, letterhead and envelopes

```html
<!DOCTYPE html>
<html lang="en">
<head>
<meta charset="utf-8">
<title>Solvane Care – Business Card</title>
<link href="https://fonts.googleapis.com/css2?family=Lato:wght@400;700;900&display=swap" rel="stylesheet">
<style>
  :root{
    --bg:#2e2e30;
    --card:#ffffff;
    --card-shade:#eef0f2;
    --blue:#1f5aa6;
    --blue-dark:#17477f;
    --orange:#e8661a;
    --ink:#222;
  }
  *{margin:0;padding:0;box-sizing:border-box}
  html,body{width:1200px;height:997px;overflow:hidden}
  body{background:var(--bg);font-family:'Lato',sans-serif;position:relative}
  .card{
    position:absolute;width:540px;height:308px;
    background:linear-gradient(160deg,var(--card) 55%,var(--card-shade));
    border-radius:3px;overflow:hidden;
    box-shadow:0 18px 40px rgba(0,0,0,.45);
  }
  .card--front{left:90px;top:120px}
  .card--back{left:570px;top:540px}
  .card__band{position:absolute;left:0;bottom:0;width:100%;height:40px}
  .brand{display:flex;align-items:center;gap:10px;font-weight:700;color:var(--blue);letter-spacing:-.5px}
  .brand__dot{width:14px;height:14px;border-radius:50%;background:var(--orange)}
  .card--front .brand{position:absolute;left:120px;top:118px;font-size:50px}
  .card--back .brand{position:absolute;left:34px;top:132px;font-size:34px}
  .card--back .brand__dot{width:10px;height:10px}
  .divider{position:absolute;left:292px;top:28px;width:3px;height:190px;
    background:linear-gradient(var(--blue) 0%,rgba(31,90,166,0) 100%)}
  .details{position:absolute;left:318px;top:30px;color:var(--ink)}
  .details__name{font-weight:900;color:var(--orange);font-size:17px;letter-spacing:.5px}
  .details__role{font-weight:700;font-size:12px;margin-top:1px}
  .details__address{font-weight:700;color:var(--blue);font-size:12px;line-height:1.35;margin-top:26px}
  .details__list{list-style:none;margin-top:8px}
  .details__list li{display:flex;align-items:center;gap:10px;font-size:13px;line-height:22px}
  .details__list svg{width:13px;height:13px;fill:var(--orange);flex:none}
</style>
</head>
<body>

<section class="card card--front" aria-label="Card front">
  <div class="brand"><span class="brand__dot"></span>Solvane Care</div>
  <svg class="card__band" viewBox="0 0 540 40" preserveAspectRatio="none" aria-hidden="true">
    <path d="M0 30 L300 30 L300 40 L0 40Z" fill="var(--blue)"/>
    <path d="M290 30 L540 4 L540 40 L0 40 L0 36 L290 36Z" fill="var(--blue-dark)" opacity="0"/>
    <path d="M0 31 H540 V40 H0Z" fill="var(--blue)"/>
    <path d="M318 22 Q322 12 336 12 H540 V22Z" fill="var(--orange)"/>
  </svg>
</section>

<section class="card card--back" aria-label="Card back">
  <div class="brand"><span class="brand__dot"></span>Solvane Care</div>
  <div class="divider"></div>
  <div class="details">
    <p class="details__name">MARISA</p>
    <p class="details__role">Designation</p>
    <p class="details__address">Via dei Tigli, 14<br>60035 Jesi (AN), Italy</p>
    <ul class="details__list">
      <li><svg viewBox="0 0 16 16"><path d="M2 6c0-2 3-3 6-3s6 1 6 3l-3 1-1-2H6L5 7 2 6zm2 2h8l1 6H3z"/></svg>+39 333 4821907</li>
      <li><svg viewBox="0 0 16 16"><path d="M4 1l3 3-2 2c1 2 3 4 5 5l2-2 3 3-2 3C7 14 2 9 1 3z"/></svg>(+123) 555 0142</li>
      <li><svg viewBox="0 0 16 16"><path d="M1 3h14v10H1zm1 1v1l6 4 6-4V4z"/></svg>info@solvanecare.com</li>
      <li><svg viewBox="0 0 16 16"><path d="M6 10l4-4 1 1-4 4zM3 9l2-2 1 1-2 2 2 2 2-2 1 1-2 2c-1 1-2 1-3 0l-1-1c-1-1-1-2 0-3zm10-2l-2 2-1-1 2-2-2-2-2 2-1-1 2-2c1-1 2-1 3 0l1 1c1 1 1 2 0 3z"/></svg>www.solvanecare.com</li>
    </ul>
  </div>
  <svg class="card__band" viewBox="0 0 540 40" preserveAspectRatio="none" aria-hidden="true">
    <path d="M0 31 H540 V40 H0Z" fill="var(--blue)"/>
    <path d="M318 22 Q322 12 336 12 H540 V22Z" fill="var(--orange)"/>
  </svg>
</section>

</body>
</html>
```